design a construction company business card

Design business card around our logo. Card must have all the typical info: name, title, address, phone, email, business name, etc. Somewhere on the card I would like to see our motto "Built on integrity... Inspired by commitment." Consider adding a splash of bright orange to the card to complement the blues and silvers/grays in the logo. We are open to metallic inks, textures, etc. We would like to see options on both light and dark backgrounds. The font in the logo is Euro Technic Extended Regular.

```html
<!DOCTYPE html>
<html lang="en">
<head>
<meta charset="utf-8">
<title>Hollis Contracting, Inc. – Business Card</title>
<link href="https://fonts.googleapis.com/css2?family=Exo+2:wght@400;700&display=swap" rel="stylesheet">
<style>
  :root {
    --stage: #3a3a3c;
    --stage-dark: #1e1e20;
    --card: #2a2a2c;
    --card-edge: #1f1f21;
    --brand-dark: #141416;
    --brand-blue: #2f64c8;
    --band-blue: #0b4fa8;
    --name-blue: #9fcdfa;
    --white: #ffffff;
    --address-grey: #b9b9bd;
    --motto-blue: #1f6fd6;
  }
  * { box-sizing: border-box; margin: 0; padding: 0; }
  html, body { width: 1200px; height: 1000px; overflow: hidden; }
  body {
    background: radial-gradient(ellipse at 60% 40%, var(--stage) 0%, var(--stage-dark) 100%);
    position: relative;
    font-family: "Exo 2", sans-serif;
  }
  .card {
    position: absolute;
    left: 250px;
    width: 700px;
    height: 400px;
    border-radius: 28px;
    background: linear-gradient(160deg, #303033 0%, var(--card) 60%, var(--card-edge) 100%);
    box-shadow: 0 18px 40px rgba(0,0,0,0.55);
    overflow: hidden;
  }
  .card--back { top: 60px; }
  .card--front { top: 530px; }

  .brand {
    position: absolute;
    left: 0; right: 0;
    display: flex;
    justify-content: center;
    align-items: center;
    gap: 14px;
    font-family: "Exo 2", sans-serif;
    font-weight: 700;
    font-size: 40px;
    line-height: 1;
  }
  .brand__mark { width: 24px; height: 24px; flex: none; }
  .card--back .brand { top: 160px; color: var(--brand-dark); }
  .card--back .brand__mark { background: var(--brand-dark); }
  .card--front .brand { top: 80px; color: var(--brand-blue); }
  .card--front .brand__mark { background: var(--brand-blue); }

  .motto {
    position: absolute;
    top: 290px; left: 0; right: 0;
    text-align: center;
    font-size: 16px;
    font-weight: 700;
    letter-spacing: 1.5px;
    color: var(--motto-blue);
    text-transform: uppercase;
  }

  .band {
    position: absolute;
    top: 200px; left: 0;
    width: 100%; height: 130px;
    background: var(--band-blue);
  }
  .person {
    position: absolute;
    top: 28px; left: 0;
    width: 330px;
    text-align: right;
  }
  .person__name { font-size: 31px; font-weight: 700; color: var(--name-blue); letter-spacing: 0.5px; }
  .person__title { font-size: 18px; color: var(--white); margin-top: 4px; }
  .band__divider {
    position: absolute;
    top: 22px; left: 358px;
    width: 2px; height: 86px;
    background: var(--white);
  }
  .contacts {
    position: absolute;
    top: 24px; left: 380px;
    list-style: none;
  }
  .contacts li {
    display: flex; align-items: center; gap: 10px;
    font-size: 18px; color: var(--white);
    height: 28px;
  }
  .contacts svg { width: 14px; height: 14px; flex: none; }
  .address {
    position: absolute;
    top: 350px; left: 0; right: 0;
    text-align: center;
    font-size: 18px;
    color: var(--address-grey);
    letter-spacing: 0.5px;
  }
</style>
</head>
<body>

  <section class="card card--back" aria-label="Card back">
    <div class="brand">
      <span class="brand__mark" aria-hidden="true"></span>
      <span class="brand__name">Hollis Contracting, Inc.</span>
    </div>
    <p class="motto">Built on integrity... Inspired by commitment.</p>
  </section>

  <section class="card card--front" aria-label="Card front">
    <div class="brand">
      <span class="brand__mark" aria-hidden="true"></span>
      <span class="brand__name">Hollis Contracting, Inc.</span>
    </div>
    <div class="band">
      <div class="person">
        <p class="person__name">Daniel Marsh</p>
        <p class="person__title">Managing Director</p>
      </div>
      <div class="band__divider"></div>
      <ul class="contacts">
        <li>
          <svg viewBox="0 0 24 24" fill="#ffffff" aria-hidden="true"><path d="M6.6 10.8a15.1 15.1 0 0 0 6.6 6.6l2.2-2.2a1 1 0 0 1 1-.25 11.4 11.4 0 0 0 3.6.57 1 1 0 0 1 1 1V20a1 1 0 0 1-1 1A17 17 0 0 1 3 4a1 1 0 0 1 1-1h3.5a1 1 0 0 1 1 1c0 1.25.2 2.45.57 3.57a1 1 0 0 1-.25 1z"/></svg>
          500.014.2100
        </li>
        <li>
          <svg viewBox="0 0 24 24" fill="#ffffff" aria-hidden="true"><path d="M2 5h20v14H2z M2 5l10 8 10-8" stroke="#0b4fa8" stroke-width="1.5"/></svg>
          daniel@holliscontract.com
        </li>
        <li>
          <svg viewBox="0 0 24 24" fill="none" stroke="#ffffff" stroke-width="2" aria-hidden="true"><circle cx="12" cy="12" r="10"/><path d="M2 12h20M12 2a15 15 0 0 1 0 20M12 2a15 15 0 0 0 0 20"/></svg>
          www.holliscontract.com
        </li>
      </ul>
    </div>
    <p class="address">2480 Harbor Avenue N.Y. Eastfield AB TIR</p>
  </section>

</body>
</html>
```